New Business Card Design for Manufacturing

We are an engineering/manufacturing company that offers Advanced machining/assembly/engineering services, as well as innovative products for the heavy duty engine cooling markets.

We are looking to get a new business card designed that is clean and modern looking, but still fits the wide range of technical/skilled work we do.

- We hope to use this design as the base for other design work in new Presentations, web, and print work.

Industry/Entity Type

Engineering

Contact Information for Business Card

Our preferred color of blue is (RGB) 22/71/159 but can vary slightly from that color. Our content will be our Logo and full company name (Vantrell Forge Works, Inc.), company address, name, job title, phone number with extension, cell number, fax number, website, and email address on the cards.
We'd like the full company name next to the logo, but we are open to other interpretations of that layout.
Preferably, we would like the back side to be clean with just our logo, and the front to contain all of the contact information.

Colors
2f74b4
0355a3
85abd2

Requirements
Must have
• - Logo, company name, needed content - We are open to interpretation beyond that.
• - Standard size business card.
• - Horizontal orientation.
• - Enough space for lengthy names / job titles (for example, a job title could read "Directory of Human Resources" or "V.P. of Governmental Affairs"). We need this to look clean, whether the title be short (CEO) or long (as described above).

```html
<!DOCTYPE html>
<html lang="en">
<head>
<meta charset="utf-8">
<title>Vantrell Forge Works – Business Card</title>
<link rel="stylesheet" href="https://fonts.googleapis.com/css2?family=Roboto:ital,wght@0,400;0,500;0,700;0,900;1,700;1,900&display=swap">
<style>
  :root {
    --brand-blue: #1050a0;
    --card-white: #f4f4f4;
    --card-grey: #7b8187;
    --tag-grey: #7a7d80;
    --ink-white: #ffffff;
    --page-bg: #e8e6e2;
  }
  * { margin: 0; padding: 0; box-sizing: border-box; }
  html, body { width: 1200px; height: 960px; overflow: hidden; }
  body {
    background: var(--page-bg);
    position: relative;
    font-family: "Roboto", Arial, sans-serif;
  }
  .card {
    position: absolute;
    width: 600px;
    height: 343px;
    border-radius: 22px;
    overflow: hidden;
  }
  .card-front { left: 302px; top: 128px; background: var(--card-white); }
  .card-back { left: 299px; top: 488px; background: var(--card-grey); }

  .front-panel { position: absolute; inset: 0; width: 600px; height: 343px; }

  .front-brand { position: absolute; left: 33px; top: 140px; }
  .brand-mark {
    font-weight: 700;
    font-size: 76px;
    line-height: 76px;
    letter-spacing: 2px;
  }
  .front-brand .brand-mark { color: var(--brand-blue); }
  .brand-tagline {
    font-weight: 700;
    font-style: italic;
    font-size: 14px;
    letter-spacing: 0.2px;
    margin-top: 4px;
  }
  .front-brand .brand-tagline { color: var(--tag-grey); }

  .contact {
    position: absolute;
    right: 45px;
    top: 86px;
    text-align: right;
    color: var(--ink-white);
  }
  .contact-name { font-weight: 500; font-size: 25px; line-height: 28px; letter-spacing: 0.3px; }
  .contact-title { font-size: 14.5px; line-height: 20px; margin-top: 2px; }
  .contact-address { font-size: 14.5px; line-height: 18px; margin-top: 10px; }
  .contact-lines { list-style: none; margin-top: 9px; margin-right: -23px; }
  .contact-lines li {
    display: flex;
    justify-content: flex-end;
    align-items: center;
    font-size: 14.5px;
    line-height: 19px;
  }
  .contact-lines svg { width: 14px; height: 14px; margin-left: 8px; flex: none; }

  .back-brand { position: absolute; left: 106px; top: 126px; color: var(--ink-white); }
  .back-brand .brand-tagline { color: var(--ink-white); }
  .company-name {
    position: absolute;
    left: 348px;
    top: 133px;
    color: var(--ink-white);
    font-weight: 900;
    font-style: italic;
    font-size: 18px;
    line-height: 19px;
    text-transform: uppercase;
  }
  .company-name small { font-size: 8px; margin-left: 3px; }
</style>
</head>
<body>
  <section class="card card-front" aria-label="Business card front">
    <svg class="front-panel" viewBox="0 0 600 343" aria-hidden="true">
      <polygon points="353,0 600,0 600,343 255,343" fill="var(--brand-blue)"/>
    </svg>

    <div class="front-brand">
      <div class="brand-mark">VFW</div>
      <div class="brand-tagline">BUILDING WHAT'S NEXT</div>
    </div>

    <div class="contact">
      <div class="contact-name">DANA WHITLOCK</div>
      <div class="contact-title">V.P. of Governmental Affairs</div>
      <div class="contact-address">4120 Larkspur Road<br>Fairbanks, Alaska 34812</div>
      <ul class="contact-lines">
        <li>555 210 4417
          <svg viewBox="0 0 14 14" aria-label="Phone"><path d="M3 1.5l2 2.6-1.2 1.4c.8 1.7 2 2.9 3.7 3.7l1.4-1.2 2.6 2-1 2c-5 0-9-4-9-9z" fill="#fff"/></svg>
        </li>
        <li>555 318 6652
          <svg viewBox="0 0 14 14" aria-label="Mobile"><rect x="3.5" y="0.8" width="7" height="12.4" rx="1.2" fill="none" stroke="#fff" stroke-width="1.4"/><circle cx="7" cy="11" r="0.8" fill="#fff"/></svg>
        </li>
        <li>dana@vantrellforge.com
          <svg viewBox="0 0 14 14" aria-label="Email"><rect x="1" y="3" width="12" height="8.5" fill="#fff"/><path d="M1 3l6 4.6L13 3" fill="none" stroke="var(--brand-blue)" stroke-width="1.2"/></svg>
        </li>
        <li>www.vantrellforge.com
          <svg viewBox="0 0 14 14" aria-label="Website"><circle cx="7" cy="7" r="6" fill="#fff"/><path d="M4 4.5c1.5 0 2 1 1.5 2S6 8.5 7 9M9.5 3.5c-.5 1 0 2 1.5 2.5" fill="none" stroke="var(--brand-blue)" stroke-width="1.2"/></svg>
        </li>
      </ul>
    </div>
  </section>

  <section class="card card-back" aria-label="Business card back">
    <div class="back-brand">
      <div class="brand-mark">VFW</div>
      <div class="brand-tagline">BUILDING WHAT'S NEXT</div>
    </div>
    <div class="company-name">Vantrell<br>Forge<br>Works<small>INC</small></div>
  </section>
</body>
</html>
```